Delivery Performance Dashboard for Web Portal

We need you to design a dashboard for our web portal. We deliver sand and stone to construction jobsites. The attached screenshot is from our current web portal dashboard . It shows how much material has been delivered from an order.

Dump trucks will deliver multiple loads during the day and the dispatcher uses the dashboard to monitor if they need to add more trucks or less trucks to fulfill the order. An example would be, I need to ship 1,000 tons of sand to a jobsite and I plan to use 10 trucks during the day and that it will take 10 hours of hauling to complete the job. After 5 hours of hauling (50% the day is over), I should have delivered 500 tons of sand (50% of the order). But maybe there is a lot of traffic, and I only have delivered 300 tons. The dashboard will show that I am behind schedule and I might need to add 2 more trucks to the job.

Industry/Entity Type

Construction

Font styles to use
Sans Serif

Requirements
Must have
• We need a progress bar showing how much material has been delivered, how much material was requested to be delivered total and how much material should have been delivered at the current time. The goal is to show the user if the deliveries are ahead or behind the expected pace and why.
Nice to have
• The icons for plant, driving and jobsite show if the actual times have exceeded or beaten the planned times. Maybe you have other ideas to show the user if the trucks are sitting longer on the jobsite, at the plant to get loaded or driving to and from the jobsite.

```html
<!DOCTYPE html>
<html lang="en">
<head>
<meta charset="utf-8">
<title>Dump Trucks – Delivery Dashboard</title>
<link href="https://fonts.googleapis.com/css2?family=IBM+Plex+Sans:wght@400;500;600;700&display=swap" rel="stylesheet">
<style>
:root{
  --stage:#333333;
  --teal:#06a98f;
  --teal-dark:#05957e;
  --teal-line:#0a9c84;
  --accent:#f0883a;
  --page:#f4f3f4;
  --card:#ffffff;
  --card-head:#5b5b5b;
  --ink:#222222;
  --muted:#555555;
  --rule:#e3e3e3;
  --track:#e1e1e1;
  --up:#e23b3b;
  --late:#e0631f;
}
*{box-sizing:border-box;margin:0;padding:0}
html,body{width:767px;height:1200px;overflow:hidden}
body{background:var(--stage);font-family:"IBM Plex Sans",Arial,sans-serif;color:var(--ink);position:relative}
.screen{position:absolute;left:46px;width:681px;height:527px;display:flex;background:var(--page);overflow:hidden}
.screen--list{top:45px}
.screen--detail{top:619px}
.sidebar{width:90px;background:var(--teal);flex:none;position:relative;z-index:3}
.brand{height:57px;display:flex;align-items:center;padding-left:8px;color:#fff;font-weight:700;font-size:9.4px;letter-spacing:.2px}
.nav{list-style:none}
.nav li{height:26.5px;display:flex;align-items:center;gap:7px;padding-left:6px;color:#fff;font-weight:600;font-size:6.8px;letter-spacing:.3px;border-bottom:1px solid var(--teal-line)}
.nav li svg{width:10px;height:10px;flex:none}
.nav li.active{background:#fff;color:var(--teal);border-left:2px solid var(--accent);padding-left:4px}
.nav li.blank{height:25px}
.main{flex:1;position:relative}
.topbar{height:25px;background:#fff;display:flex;justify-content:flex-end;align-items:center;padding-right:11px;gap:4px}
.avatar{width:13px;height:13px;border-radius:50%;background:linear-gradient(#e9c9a8,#6b4a35);border:1.2px solid var(--teal)}
.user{font-size:4.6px;font-weight:600;line-height:6.2px;letter-spacing:.2px}
.caret{width:6px;height:6px;margin-left:4px}
.grid{display:grid;grid-template-columns:repeat(4,135px);column-gap:8px;row-gap:9px;padding:16px 0 0 16px}
.card{background:var(--card);height:212px;display:flex;flex-direction:column}
.card-head{height:12.5px;background:var(--card-head);display:flex;justify-content:space-between;align-items:center;color:#fff;font-size:5.8px;font-weight:700;padding-left:6px}
.badge{height:100%;background:var(--teal);display:flex;align-items:center;gap:2px;padding:0 4px;font-size:4.7px;font-weight:600;letter-spacing:.2px}
.badge svg{width:5px;height:5px}
.row{margin:0 6px;padding-left:5px;border-bottom:1px solid var(--rule);display:flex;flex-direction:column;justify-content:center;font-size:5.4px;line-height:7.2px}
.row:last-child{border-bottom:none}
.label{font-weight:600;text-transform:uppercase}
.r-origin{height:26px}.r-dest{height:24.5px}.r-cust{height:28px}.r-tons{height:36px}.r-wait{height:31px}.r-rem{height:27px}.r-diff{height:27px}
.bar{height:3px;background:var(--track);border-radius:2px;margin:6px 6px 4px 0}
.bar i{display:block;height:100%;width:54%;background:var(--teal);border-radius:2px}
.bar-meta{display:flex;justify-content:space-between;font-size:4.4px;padding-right:6px}
.waits{display:flex;gap:8px;margin-top:4px;align-items:center}
.waits span{display:flex;align-items:center;gap:1.5px}
.waits svg{height:6px}
.good{color:var(--teal);font-weight:600}
.late{color:var(--late);font-weight:600}
.footer{position:absolute;left:0;right:0;top:502px;text-align:center;font-size:6px}
.dim{position:absolute;inset:0;background:rgba(60,60,60,.2);z-index:2}
.popover{position:absolute;left:18px;top:197px;width:115px;background:#fff;z-index:4;box-shadow:0 1px 4px rgba(0,0,0,.25);padding:0 7px}
.popover::before{content:"";position:absolute;top:-4px;left:19px;border:4px solid transparent;border-top:0;border-bottom-color:#fff}
.pop-title{font-size:4.8px;height:18px;display:flex;align-items:center;border-bottom:1px solid var(--rule);margin-right:0}
.pop-row{height:25px;display:flex;align-items:center;gap:5px;border-bottom:1px solid var(--rule);font-size:4.8px;line-height:6.8px;margin-left:-7px;padding-left:6px;margin-right:-7px;padding-right:11px}
.pop-row:last-child{border-bottom:none}
.pop-row:first-of-type{margin-top:4px}
.pop-dot{width:12px;height:12px;border-radius:50%;background:var(--teal);display:flex;align-items:center;justify-content:center;flex:none}
.pop-dot svg{width:6px;height:6px}
.pop-text{flex:1}
.pop-text b{font-weight:500}
.pop-actual{align-self:flex-end;margin-bottom:4px}
</style>
</head>
<body>
<svg width="0" height="0" style="position:absolute">
  <defs>
    <symbol id="i-home" viewBox="0 0 10 10"><path d="M1 5 5 1.5 9 5M2.3 4v4.8h5.4V4M4.2 8.8V6.3h1.6v2.5" fill="none" stroke="currentColor" stroke-width=".8"/></symbol>
    <symbol id="i-user" viewBox="0 0 10 10"><circle cx="5" cy="3.2" r="2.1" fill="none" stroke="currentColor" stroke-width=".8"/><path d="M1.3 9.5c.4-2.3 1.9-3.4 3.7-3.4s3.3 1.1 3.7 3.4" fill="none" stroke="currentColor" stroke-width=".8"/></symbol>
    <symbol id="i-cal" viewBox="0 0 10 10"><rect x="1" y="1.8" width="7" height="7" fill="none" stroke="currentColor" stroke-width=".8"/><path d="M1 3.6h7M3 1v1.6M6 1v1.6" stroke="currentColor" stroke-width=".8"/><circle cx="7.6" cy="7.6" r="1.8" fill="var(--teal)" stroke="currentColor" stroke-width=".7"/></symbol>
    <symbol id="i-exp" viewBox="0 0 10 10"><circle cx="5" cy="5" r="4" fill="none" stroke="currentColor" stroke-width=".7"/><circle cx="5" cy="5" r="2.6" fill="none" stroke="currentColor" stroke-width=".7"/><circle cx="5" cy="5" r="1" fill="currentColor"/></symbol>
    <symbol id="i-perf" viewBox="0 0 10 10"><path d="M1 9.3h8.5M1.5 9.3V7h1.5v2.3M4.2 9.3V5.5h1.5v3.8M7 9.3V4h1.5v5.3M1.5 5 4 3l1.8 1.2L9 1.2" fill="none" stroke="currentColor" stroke-width=".7"/></symbol>
    <symbol id="i-rep" viewBox="0 0 10 10"><rect x="2" y="1" width="6" height="8.3" fill="none" stroke="currentColor" stroke-width=".8"/><path d="M3.3 3h3.4M3.3 4.6h3.4M3.3 6.2h3.4M3.3 7.8h2" stroke="currentColor" stroke-width=".7"/></symbol>
    <symbol id="i-gear" viewBox="0 0 10 10"><circle cx="5" cy="5" r="3" fill="currentColor"/><path d="M5 .6v1.6M5 7.8v1.6M.6 5h1.6M7.8 5h1.6M1.9 1.9 3 3M7 7l1.1 1.1M1.9 8.1 3 7M7 3l1.1-1.1" stroke="currentColor" stroke-width="1.4"/><circle cx="5" cy="5" r="1.1" fill="var(--teal)"/></symbol>
    <symbol id="i-tick" viewBox="0 0 6 6"><path d="M.8 3.2 2.3 4.6 5.2 1.4" fill="none" stroke="#fff" stroke-width="1"/></symbol>
    <symbol id="i-plant" viewBox="0 0 9 7"><path d="M0 7V1.5h1.2v2L3 2.2v1.3l1.8-1.3v1.3l1.8-1.3V7z" fill="#8a8a8a"/></symbol>
    <symbol id="i-truck" viewBox="0 0 10 7"><path d="M0 1h6v4.5H0zM6 2.5h2.3L10 4v1.5H6z" fill="#8a8a8a"/><circle cx="2" cy="6" r="1" fill="#8a8a8a"/><circle cx="8" cy="6" r="1" fill="#8a8a8a"/></symbol>
    <symbol id="i-pin" viewBox="0 0 6 8"><path d="M3 .3A2.6 2.6 0 0 0 .4 2.9C.4 5 3 7.7 3 7.7S5.6 5 5.6 2.9A2.6 2.6 0 0 0 3 .3z" fill="none" stroke="#6a6a6a" stroke-width=".9"/><circle cx="3" cy="2.9" r=".9" fill="#6a6a6a"/></symbol>
    <symbol id="i-up" viewBox="0 0 4 3"><path d="M0 3 2 0 4 3z" fill="var(--up)"/></symbol>
    <symbol id="i-down" viewBox="0 0 4 3"><path d="M0 0h4L2 3z" fill="var(--teal)"/></symbol>
  </defs>
</svg>

<!-- Screen: overview -->
<section class="screen screen--list">
  <aside class="sidebar">
    <div class="brand">DUMP TRUCKS</div>
    <ul class="nav">
      <li class="active"><svg><use href="#i-home"/></svg>DASHBOARD</li>
      <li><svg><use href="#i-user"/></svg>EMPLOYEES</li>
      <li><svg><use href="#i-cal"/></svg>CALENDAR</li>
      <li><svg><use href="#i-exp"/></svg>EXPENSES</li>
      <li><svg><use href="#i-perf"/></svg>PERFORMANCE</li>
      <li><svg><use href="#i-rep"/></svg>REPORTS</li>
      <li><svg><use href="#i-gear"/></svg>SETTINGS</li>
      <li class="blank"></li><li class="blank"></li>
    </ul>
  </aside>
  <main class="main">
    <header class="topbar">
      <div class="avatar" role="img" aria-label="User avatar"></div>
      <div class="user">ADMIN, DEMO<br>HR ADMINISTRATOR</div>
      <svg class="caret" viewBox="0 0 6 6"><path d="M1 2 3 4 5 2" fill="none" stroke="#555" stroke-width=".8"/></svg>
    </header>
    <div class="grid">
      <article class="card"><div class="card-head">#17746<span class="badge"><svg><use href="#i-tick"/></svg>APPROVED</span></div><div class="row r-origin"><span class="label">Origin</span>Harlow Aggregate Plant</div><div class="row r-dest"><span class="label">Destination</span>BZJV - 185 from mm 77-98</div><div class="row r-cust"><span class="label">Customer</span>Brennan Builders = North Division</div><div class="row r-tons"><span class="label">Tons</span><div class="bar"><i></i></div><div class="bar-meta"><span>722.57/1500</span><span>7.30am-5.00pm</span></div></div><div class="row r-wait"><span class="label">Wait Time</span><div class="waits"><span><svg width="7"><use href="#i-plant"/></svg><svg width="3"><use href="#i-up"/></svg></span><span><svg width="8"><use href="#i-truck"/></svg><svg width="3"><use href="#i-up"/></svg></span><span><svg width="5"><use href="#i-pin"/></svg><svg width="3"><use href="#i-down"/></svg></span></div></div><div class="row r-rem"><span class="label">Remaining</span><span class="good">+1.25 hrs</span></div><div class="row r-diff"><span>+ / -</span><span class="late">-31</span></div></article>
      <article class="card"><div class="card-head">#6587<span class="badge"><svg><use href="#i-tick"/></svg>APPROVED</span></div><div class="row r-origin"><span class="label">Origin</span>Harlow Aggregate Plant</div><div class="row r-dest"><span class="label">Destination</span>BZJV - 185 from mm 77-98</div><div class="row r-cust"><span class="label">Customer</span>Brennan Builders = North Division</div><div class="row r-tons"><span class="label">Tons</span><div class="bar"><i></i></div><div class="bar-meta"><span>722.57/1500</span><span>7.30am-5.00pm</span></div></div><div class="row r-wait"><span class="label">Wait Time</span><div class="waits"><span><svg width="7"><use href="#i-plant"/></svg><svg width="3"><use href="#i-up"/></svg></span><span><svg width="8"><use href="#i-truck"/></svg><svg width="3"><use href="#i-up"/></svg></span><span><svg width="5"><use href="#i-pin"/></svg><svg width="3"><use href="#i-down"/></svg></span></div></div><div class="row r-rem"><span class="label">Remaining</span><span class="good">+1.25 hrs</span></div><div class="row r-diff"><span>+ / -</span><span class="late">-31</span></div></article>
      <article class="card"><div class="card-head">#254879<span class="badge"><svg><use href="#i-tick"/></svg>APPROVED</span></div><div class="row r-origin"><span class="label">Origin</span>Harlow Aggregate Plant</div><div class="row r-dest"><span class="label">Destination</span>BZJV - 185 from mm 77-98</div><div class="row r-cust"><span class="label">Customer</span>Brennan Builders = North Division</div><div class="row r-tons"><span class="label">Tons</span><div class="bar"><i></i></div><div class="bar-meta"><span>722.57/1500</span><span>7.30am-5.00pm</span></div></div><div class="row r-wait"><span class="label">Wait Time</span><div class="waits"><span><svg width="7"><use href="#i-plant"/></svg><svg width="3"><use href="#i-up"/></svg></span><span><svg width="8"><use href="#i-truck"/></svg><svg width="3"><use href="#i-up"/></svg></span><span><svg width="5"><use href="#i-pin"/></svg><svg width="3"><use href="#i-down"/></svg></span></div></div><div class="row r-rem"><span class="label">Remaining</span><span class="good">+1.25 hrs</span></div><div class="row r-diff"><span>+ / -</span><span class="late">-31</span></div></article>
      <article class="card"><div class="card-head">#162451<span class="badge"><svg><use href="#i-tick"/></svg>APPROVED</span></div><div class="row r-origin"><span class="label">Origin</span>Harlow Aggregate Plant</div><div class="row r-dest"><span class="label">Destination</span>BZJV - 185 from mm 77-98</div><div class="row r-cust"><span class="label">Customer</span>Brennan Builders = North Division</div><div class="row r-tons"><span class="label">Tons</span><div class="bar"><i></i></div><div class="bar-meta"><span>722.57/1500</span><span>7.30am-5.00pm</span></div></div><div class="row r-wait"><span class="label">Wait Time</span><div class="waits"><span><svg width="7"><use href="#i-plant"/></svg><svg width="3"><use href="#i-up"/></svg></span><span><svg width="8"><use href="#i-truck"/></svg><svg width="3"><use href="#i-up"/></svg></span><span><svg width="5"><use href="#i-pin"/></svg><svg width="3"><use href="#i-down"/></svg></span></div></div><div class="row r-rem"><span class="label">Remaining</span><span class="good">+1.25 hrs</span></div><div class="row r-diff"><span>+ / -</span><span class="late">-31</span></div></article>
      <article class="card"><div class="card-head">#17746<span class="badge"><svg><use href="#i-tick"/></svg>APPROVED</span></div><div class="row r-origin"><span class="label">Origin</span>Harlow Aggregate Plant</div><div class="row r-dest"><span class="label">Destination</span>BZJV - 185 from mm 77-98</div><div class="row r-cust"><span class="label">Customer</span>Brennan Builders = North Division</div><div class="row r-tons"><span class="label">Tons</span><div class="bar"><i></i></div><div class="bar-meta"><span>722.57/1500</span><span>7.30am-5.00pm</span></div></div><div class="row r-wait"><span class="label">Wait Time</span><div class="waits"><span><svg width="7"><use href="#i-plant"/></svg><svg width="3"><use href="#i-up"/></svg></span><span><svg width="8"><use href="#i-truck"/></svg><svg width="3"><use href="#i-up"/></svg></span><span><svg width="5"><use href="#i-pin"/></svg><svg width="3"><use href="#i-down"/></svg></span></div></div><div class="row r-rem"><span class="label">Remaining</span><span class="good">+1.25 hrs</span></div><div class="row r-diff"><span>+ / -</span><span class="late">-31</span></div></article>
      <article class="card"><div class="card-head">#17746<span class="badge"><svg><use href="#i-tick"/></svg>APPROVED</span></div><div class="row r-origin"><span class="label">Origin</span>Harlow Aggregate Plant</div><div class="row r-dest"><span class="label">Destination</span>BZJV - 185 from mm 77-98</div><div class="row r-cust"><span class="label">Customer</span>Brennan Builders = North Division</div><div class="row r-tons"><span class="label">Tons</span><div class="bar"><i></i></div><div class="bar-meta"><span>722.57/1500</span><span>7.30am-5.00pm</span></div></div><div class="row r-wait"><span class="label">Wait Time</span><div class="waits"><span><svg width="7"><use href="#i-plant"/></svg><svg width="3"><use href="#i-up"/></svg></span><span><svg width="8"><use href="#i-truck"/></svg><svg width="3"><use href="#i-up"/></svg></span><span><svg width="5"><use href="#i-pin"/></svg><svg width="3"><use href="#i-down"/></svg></span></div></div><div class="row r-rem"><span class="label">Remaining</span><span class="good">+1.25 hrs</span></div><div class="row r-diff"><span>+ / -</span><span class="late">-31</span></div></article>
      <article class="card"><div class="card-head">#17746<span class="badge"><svg><use href="#i-tick"/></svg>APPROVED</span></div><div class="row r-origin"><span class="label">Origin</span>Harlow Aggregate Plant</div><div class="row r-dest"><span class="label">Destination</span>BZJV - 185 from mm 77-98</div><div class="row r-cust"><span class="label">Customer</span>Brennan Builders = North Division</div><div class="row r-tons"><span class="label">Tons</span><div class="bar"><i></i></div><div class="bar-meta"><span>722.57/1500</span><span>7.30am-5.00pm</span></div></div><div class="row r-wait"><span class="label">Wait Time</span><div class="waits"><span><svg width="7"><use href="#i-plant"/></svg><svg width="3"><use href="#i-up"/></svg></span><span><svg width="8"><use href="#i-truck"/></svg><svg width="3"><use href="#i-up"/></svg></span><span><svg width="5"><use href="#i-pin"/></svg><svg width="3"><use href="#i-down"/></svg></span></div></div><div class="row r-rem"><span class="label">Remaining</span><span class="good">+1.25 hrs</span></div><div class="row r-diff"><span>+ / -</span><span class="late">-31</span></div></article>
      <article class="card"><div class="card-head">#17746<span class="badge"><svg><use href="#i-tick"/></svg>APPROVED</span></div><div class="row r-origin"><span class="label">Origin</span>Harlow Aggregate Plant</div><div class="row r-dest"><span class="label">Destination</span>BZJV - 185 from mm 77-98</div><div class="row r-cust"><span class="label">Customer</span>Brennan Builders = North Division</div><div class="row r-tons"><span class="label">Tons</span><div class="bar"><i></i></div><div class="bar-meta"><span>722.57/1500</span><span>7.30am-5.00pm</span></div></div><div class="row r-wait"><span class="label">Wait Time</span><div class="waits"><span><svg width="7"><use href="#i-plant"/></svg><svg width="3"><use href="#i-up"/></svg></span><span><svg width="8"><use href="#i-truck"/></svg><svg width="3"><use href="#i-up"/></svg></span><span><svg width="5"><use href="#i-pin"/></svg><svg width="3"><use href="#i-down"/></svg></span></div></div><div class="row r-rem"><span class="label">Remaining</span><span class="good">+1.25 hrs</span></div><div class="row r-diff"><span>+ / -</span><span class="late">-31</span></div></article>
    </div>
    <footer class="footer">Copyright © 2020 All Rights Reserved</footer>
  </main>
</section>

<!-- Screen: wait time breakdown open -->
<section class="screen screen--detail">
  <aside class="sidebar">
    <div class="brand">DUMP TRUCKS</div>
    <ul class="nav">
      <li class="active"><svg><use href="#i-home"/></svg>DASHBOARD</li>
      <li><svg><use href="#i-user"/></svg>EMPLOYEES</li>
      <li><svg><use href="#i-cal"/></svg>CALENDAR</li>
      <li><svg><use href="#i-exp"/></svg>EXPENSES</li>
      <li><svg><use href="#i-perf"/></svg>PERFORMANCE</li>
      <li><svg><use href="#i-rep"/></svg>REPORTS</li>
      <li><svg><use href="#i-gear"/></svg>SETTINGS</li>
      <li class="blank"></li><li class="blank"></li>
    </ul>
  </aside>
  <main class="main">
    <header class="topbar">
      <div class="avatar" role="img" aria-label="User avatar"></div>
      <div class="user">ADMIN, DEMO<br>HR ADMINISTRATOR</div>
      <svg class="caret" viewBox="0 0 6 6"><path d="M1 2 3 4 5 2" fill="none" stroke="#555" stroke-width=".8"/></svg>
    </header>
    <div class="grid">
      <article class="card"><div class="card-head">#17746<span class="badge"><svg><use href="#i-tick"/></svg>APPROVED</span></div><div class="row r-origin"><span class="label">Origin</span>Harlow Aggregate Plant</div><div class="row r-dest"><span class="label">Destination</span>BZJV - 185 from mm 77-98</div><div class="row r-cust"><span class="label">Customer</span>Brennan Builders = North Division</div><div class="row r-tons"><span class="label">Tons</span><div class="bar"><i></i></div><div class="bar-meta"><span>722.57/1500</span><span>7.30am-5.00pm</span></div></div><div class="row r-wait"><span class="label">Wait Time</span><div class="waits"><span><svg width="7"><use href="#i-plant"/></svg><svg width="3"><use href="#i-up"/></svg></span><span><svg width="8"><use href="#i-truck"/></svg><svg width="3"><use href="#i-up"/></svg></span><span><svg width="5"><use href="#i-pin"/></svg><svg width="3"><use href="#i-down"/></svg></span></div></div><div class="row r-rem"><span class="label">Remaining</span><span class="good">+1.25 hrs</span></div><div class="row r-diff"><span>+ / -</span><span class="late">-31</span></div></article>
      <article class="card"><div class="card-head">#6587<span class="badge"><svg><use href="#i-tick"/></svg>APPROVED</span></div><div class="row r-origin"><span class="label">Origin</span>Harlow Aggregate Plant</div><div class="row r-dest"><span class="label">Destination</span>BZJV - 185 from mm 77-98</div><div class="row r-cust"><span class="label">Customer</span>Brennan Builders = North Division</div><div class="row r-tons"><span class="label">Tons</span><div class="bar"><i></i></div><div class="bar-meta"><span>722.57/1500</span><span>7.30am-5.00pm</span></div></div><div class="row r-wait"><span class="label">Wait Time</span><div class="waits"><span><svg width="7"><use href="#i-plant"/></svg><svg width="3"><use href="#i-up"/></svg></span><span><svg width="8"><use href="#i-truck"/></svg><svg width="3"><use href="#i-up"/></svg></span><span><svg width="5"><use href="#i-pin"/></svg><svg width="3"><use href="#i-down"/></svg></span></div></div><div class="row r-rem"><span class="label">Remaining</span><span class="good">+1.25 hrs</span></div><div class="row r-diff"><span>+ / -</span><span class="late">-31</span></div></article>
      <article class="card"><div class="card-head">#254879<span class="badge"><svg><use href="#i-tick"/></svg>APPROVED</span></div><div class="row r-origin"><span class="label">Origin</span>Harlow Aggregate Plant</div><div class="row r-dest"><span class="label">Destination</span>BZJV - 185 from mm 77-98</div><div class="row r-cust"><span class="label">Customer</span>Brennan Builders = North Division</div><div class="row r-tons"><span class="label">Tons</span><div class="bar"><i></i></div><div class="bar-meta"><span>722.57/1500</span><span>7.30am-5.00pm</span></div></div><div class="row r-wait"><span class="label">Wait Time</span><div class="waits"><span><svg width="7"><use href="#i-plant"/></svg><svg width="3"><use href="#i-up"/></svg></span><span><svg width="8"><use href="#i-truck"/></svg><svg width="3"><use href="#i-up"/></svg></span><span><svg width="5"><use href="#i-pin"/></svg><svg width="3"><use href="#i-down"/></svg></span></div></div><div class="row r-rem"><span class="label">Remaining</span><span class="good">+1.25 hrs</span></div><div class="row r-diff"><span>+ / -</span><span class="late">-31</span></div></article>
      <article class="card"><div class="card-head">#162451<span class="badge"><svg><use href="#i-tick"/></svg>APPROVED</span></div><div class="row r-origin"><span class="label">Origin</span>Harlow Aggregate Plant</div><div class="row r-dest"><span class="label">Destination</span>BZJV - 185 from mm 77-98</div><div class="row r-cust"><span class="label">Customer</span>Brennan Builders = North Division</div><div class="row r-tons"><span class="label">Tons</span><div class="bar"><i></i></div><div class="bar-meta"><span>722.57/1500</span><span>7.30am-5.00pm</span></div></div><div class="row r-wait"><span class="label">Wait Time</span><div class="waits"><span><svg width="7"><use href="#i-plant"/></svg><svg width="3"><use href="#i-up"/></svg></span><span><svg width="8"><use href="#i-truck"/></svg><svg width="3"><use href="#i-up"/></svg></span><span><svg width="5"><use href="#i-pin"/></svg><svg width="3"><use href="#i-down"/></svg></span></div></div><div class="row r-rem"><span class="label">Remaining</span><span class="good">+1.25 hrs</span></div><div class="row r-diff"><span>+ / -</span><span class="late">-31</span></div></article>
      <article class="card"><div class="card-head">#17746<span class="badge"><svg><use href="#i-tick"/></svg>APPROVED</span></div><div class="row r-origin"><span class="label">Origin</span>Harlow Aggregate Plant</div><div class="row r-dest"><span class="label">Destination</span>BZJV - 185 from mm 77-98</div><div class="row r-cust"><span class="label">Customer</span>Brennan Builders = North Division</div><div class="row r-tons"><span class="label">Tons</span><div class="bar"><i></i></div><div class="bar-meta"><span>722.57/1500</span><span>7.30am-5.00pm</span></div></div><div class="row r-wait"><span class="label">Wait Time</span><div class="waits"><span><svg width="7"><use href="#i-plant"/></svg><svg width="3"><use href="#i-up"/></svg></span><span><svg width="8"><use href="#i-truck"/></svg><svg width="3"><use href="#i-up"/></svg></span><span><svg width="5"><use href="#i-pin"/></svg><svg width="3"><use href="#i-down"/></svg></span></div></div><div class="row r-rem"><span class="label">Remaining</span><span class="good">+1.25 hrs</span></div><div class="row r-diff"><span>+ / -</span><span class="late">-31</span></div></article>
      <article class="card"><div class="card-head">#17746<span class="badge"><svg><use href="#i-tick"/></svg>APPROVED</span></div><div class="row r-origin"><span class="label">Origin</span>Harlow Aggregate Plant</div><div class="row r-dest"><span class="label">Destination</span>BZJV - 185 from mm 77-98</div><div class="row r-cust"><span class="label">Customer</span>Brennan Builders = North Division</div><div class="row r-tons"><span class="label">Tons</span><div class="bar"><i></i></div><div class="bar-meta"><span>722.57/1500</span><span>7.30am-5.00pm</span></div></div><div class="row r-wait"><span class="label">Wait Time</span><div class="waits"><span><svg width="7"><use href="#i-plant"/></svg><svg width="3"><use href="#i-up"/></svg></span><span><svg width="8"><use href="#i-truck"/></svg><svg width="3"><use href="#i-up"/></svg></span><span><svg width="5"><use href="#i-pin"/></svg><svg width="3"><use href="#i-down"/></svg></span></div></div><div class="row r-rem"><span class="label">Remaining</span><span class="good">+1.25 hrs</span></div><div class="row r-diff"><span>+ / -</span><span class="late">-31</span></div></article>
      <article class="card"><div class="card-head">#17746<span class="badge"><svg><use href="#i-tick"/></svg>APPROVED</span></div><div class="row r-origin"><span class="label">Origin</span>Harlow Aggregate Plant</div><div class="row r-dest"><span class="label">Destination</span>BZJV - 185 from mm 77-98</div><div class="row r-cust"><span class="label">Customer</span>Brennan Builders = North Division</div><div class="row r-tons"><span class="label">Tons</span><div class="bar"><i></i></div><div class="bar-meta"><span>722.57/1500</span><span>7.30am-5.00pm</span></div></div><div class="row r-wait"><span class="label">Wait Time</span><div class="waits"><span><svg width="7"><use href="#i-plant"/></svg><svg width="3"><use href="#i-up"/></svg></span><span><svg width="8"><use href="#i-truck"/></svg><svg width="3"><use href="#i-up"/></svg></span><span><svg width="5"><use href="#i-pin"/></svg><svg width="3"><use href="#i-down"/></svg></span></div></div><div class="row r-rem"><span class="label">Remaining</span><span class="good">+1.25 hrs</span></div><div class="row r-diff"><span>+ / -</span><span class="late">-31</span></div></article>
      <article class="card"><div class="card-head">#17746<span class="badge"><svg><use href="#i-tick"/></svg>APPROVED</span></div><div class="row r-origin"><span class="label">Origin</span>Harlow Aggregate Plant</div><div class="row r-dest"><span class="label">Destination</span>BZJV - 185 from mm 77-98</div><div class="row r-cust"><span class="label">Customer</span>Brennan Builders = North Division</div><div class="row r-tons"><span class="label">Tons</span><div class="bar"><i></i></div><div class="bar-meta"><span>722.57/1500</span><span>7.30am-5.00pm</span></div></div><div class="row r-wait"><span class="label">Wait Time</span><div class="waits"><span><svg width="7"><use href="#i-plant"/></svg><svg width="3"><use href="#i-up"/></svg></span><span><svg width="8"><use href="#i-truck"/></svg><svg width="3"><use href="#i-up"/></svg></span><span><svg width="5"><use href="#i-pin"/></svg><svg width="3"><use href="#i-down"/></svg></span></div></div><div class="row r-rem"><span class="label">Remaining</span><span class="good">+1.25 hrs</span></div><div class="row r-diff"><span>+ / -</span><span class="late">-31</span></div></article>
    </div>
    <footer class="footer">Copyright © 2020 All Rights Reserved</footer>
    <div class="dim"></div>
    <div class="popover">
      <div class="pop-title">Avg Cycle Time : 2hr 27mins</div>
      <div class="pop-row"><span class="pop-dot"><svg viewBox="0 0 9 7"><path d="M0 7V1.5h1.2v2L3 2.2v1.3l1.8-1.3v1.3l1.8-1.3V7z" fill="#fff"/></svg></span><span class="pop-text"><b>Plat (min)</b><br>Planned : 30</span><span class="pop-actual">Actual : 33</span></div>
      <div class="pop-row"><span class="pop-dot"><svg viewBox="0 0 10 7"><path d="M0 1h6v4.5H0zM6 2.5h2.3L10 4v1.5H6z" fill="#fff"/><circle cx="2" cy="6" r="1" fill="#fff"/><circle cx="8" cy="6" r="1" fill="#fff"/></svg></span><span class="pop-text"><b>Driving (min)</b><br>Planned : 30</span><span class="pop-actual">Actual : 33</span></div>
      <div class="pop-row"><span class="pop-dot"><svg viewBox="0 0 6 8"><path d="M3 .3A2.6 2.6 0 0 0 .4 2.9C.4 5 3 7.7 3 7.7S5.6 5 5.6 2.9A2.6 2.6 0 0 0 3 .3z" fill="#fff"/><circle cx="3" cy="2.9" r=".9" fill="var(--teal)"/></svg></span><span class="pop-text"><b>Jobsite (min)</b><br>Planned : 30</span><span class="pop-actual">Actual : 33</span></div>
      <div class="pop-row"><span class="pop-dot"><svg viewBox="0 0 10 10" style="color:#fff"><use href="#i-gear"/></svg></span><span class="pop-text"><b>Equipment (min)</b><br>Planned : 30</span><span class="pop-actual">Actual : 33</span></div>
    </div>
  </main>
</section>
</body>
</html>
```